Business Card Design For A Cajun Seafood Restaurant

We are opening a cajun seafood restaurant in a week. We mainly serve cajun seafood which is orginally from Louisiana. We want design on both sides of a business card. I have menu on the website. You can go to www.reednkettle.example to check out our menu.

Restaurant name: Reed N' Kettle
Phone: +1 (555) 304-7712
Address: 48206 Ludlow Row, #7, Bexmoor Flats, Ca90000
Email: reednkettle@mailbox.example
Website: www.reednkettle.example

Maybe add social media icons (facebook, instagram) if looks nice on the business card.
facebook.com/reednkettle
instagram.com/reednkettle or @reednkettle

Attached is the logo and other business card samples that I like.

```html
<!DOCTYPE html>
<html lang="en">
<head>
<meta charset="utf-8">
<title>Reed N' Kettle — Business Card</title>
<link href="https://fonts.googleapis.com/css2?family=Roboto:wght@400;500;700&display=swap" rel="stylesheet">
<style>
  :root {
    --backdrop: #e8e8e7;
    --kraft: #c8a57a;
    --kraft-light: #d2b189;
    --paper-white: #f1f1f0;
    --mustard: #d39a22;
    --crab-orange: #d0552c;
    --corn-yellow: #e8b53c;
    --ink: #1d1a17;
    --ink-soft: #2b2622;
  }
  * { box-sizing: border-box; margin: 0; padding: 0; }
  html, body {
    width: 1200px; height: 576px; overflow: hidden;
    background: var(--backdrop);
    font-family: "Roboto", Arial, sans-serif;
    color: var(--ink);
  }
  .canvas { position: relative; width: 1200px; height: 576px; }
  .card {
    position: absolute; top: 140px;
    width: 484px; height: 294px;
    border-radius: 6px; overflow: hidden;
    background: radial-gradient(circle at 40% 35%, var(--kraft-light), var(--kraft) 75%);
  }
  .card--front { left: 82px; }
  .card--back { left: 602px; }

  /* Front */
  .mascot-art {
    position: absolute; border-radius: 50% 50% 44% 44%;
    background: radial-gradient(circle at 50% 30%, var(--corn-yellow) 0 22%, var(--crab-orange) 40%, #b8451f 75%);
  }
  .card--front .mascot-art { left: 193px; top: 44px; width: 110px; height: 104px; }
  .wordmark {
    position: absolute; left: 0; right: 0; top: 156px; text-align: center;
  }
  .wordmark__name {
    font-weight: 700; font-size: 26px; letter-spacing: 0.5px; color: var(--ink);
  }
  .wordmark__tagline {
    margin-top: 4px; font-weight: 500; font-size: 11px; letter-spacing: 1.6px; color: var(--ink-soft);
  }
  .torn-strip { position: absolute; left: 0; bottom: 0; width: 484px; }
  .front-url {
    position: absolute; left: 0; right: 0; top: 263px; text-align: center;
    font-size: 14px; color: var(--ink);
  }

  /* Back */
  .card--back .mascot-art { left: 48px; top: 58px; width: 176px; height: 172px; }
  .contact { position: absolute; left: 270px; top: 56px; }
  .contact__name { font-weight: 700; font-size: 19px; line-height: 22px; }
  .contact__role { font-size: 11.5px; line-height: 16px; }
  .contact__address { margin-top: 16px; font-size: 12.5px; line-height: 18.5px; }
  .contact__list { list-style: none; margin-top: 8px; }
  .contact__item {
    display: flex; align-items: center; gap: 8px;
    font-size: 12.5px; line-height: 18.2px;
  }
  .contact__icon { width: 10px; height: 10px; flex: none; fill: var(--ink); }
  .social-mark { width: 9px; height: 9px; background: var(--ink); border-radius: 1.5px; flex: none; margin: 0 0.5px; }
</style>
</head>
<body>
<main class="canvas">

  <section class="card card--front">
    <div class="mascot-art" role="img" aria-label="Illustrated mascot holding an ear of corn"></div>
    <div class="wordmark">
      <div class="wordmark__name">Reed N' Kettle</div>
      <div class="wordmark__tagline">CAJUN SEAFOOD HOUSE</div>
    </div>
    <svg class="torn-strip" viewBox="0 0 484 50" height="50" aria-hidden="true">
      <path d="M0 6 L14 4 L26 8 L40 3 L58 6 L74 2 L92 7 L110 4 L128 6 L148 2 L166 6 L186 3 L204 7 L224 4 L244 6 L262 2 L282 6 L302 3 L320 7 L340 4 L360 6 L378 2 L398 6 L418 3 L436 7 L456 4 L472 6 L484 3 L484 50 L0 50 Z" fill="var(--paper-white)"/>
    </svg>
    <div class="front-url">www.reednkettle.example</div>
  </section>

  <section class="card card--back">
    <div class="mascot-art" role="img" aria-label="Illustrated mascot holding an ear of corn overhead"></div>
    <div class="contact">
      <div class="contact__name">Alden Marsh</div>
      <div class="contact__role">Director</div>
      <div class="contact__address">48206 Ludlow Row, #7,<br>Bexmoor Flats, Ca90000</div>
      <ul class="contact__list">
        <li class="contact__item">
          <svg class="contact__icon" viewBox="0 0 10 10" aria-hidden="true"><path d="M1 3 Q5 0 9 3 L8 4.5 L6.5 4 L6.5 3 L3.5 3 L3.5 4 L2 4.5 Z M2.5 5 L7.5 5 L8.5 9 L1.5 9 Z"/></svg>
          +1 (555) 304-7712
        </li>
        <li class="contact__item">
          <svg class="contact__icon" viewBox="0 0 10 10" aria-hidden="true"><path d="M0.5 2 H9.5 V8 H0.5 Z" fill="none" stroke="var(--ink)" stroke-width="1"/><path d="M0.5 2 L5 5.5 L9.5 2" fill="none" stroke="var(--ink)" stroke-width="1"/></svg>
          reednkettle@mailbox.example
        </li>
        <li class="contact__item">
          <svg class="contact__icon" viewBox="0 0 10 10" aria-hidden="true"><g fill="none" stroke="var(--ink)" stroke-width="0.9"><circle cx="5" cy="5" r="4.2"/><ellipse cx="5" cy="5" rx="1.8" ry="4.2"/><path d="M0.8 5 H9.2"/></g></svg>
          www.reednkettle.example
        </li>
        <li class="contact__item"><span class="social-mark"></span>facebook.com/reednkettle</li>
        <li class="contact__item"><span class="social-mark"></span>instagram.com/reednkettle</li>
      </ul>
    </div>
    <svg class="torn-strip" viewBox="0 0 484 26" height="26" aria-hidden="true">
      <path d="M0 6 L18 4 L36 7 L58 3 L80 6 L104 4 L126 7 L150 3 L172 6 L196 4 L220 7 L244 3 L268 6 L290 4 L314 7 L338 3 L360 6 L384 4 L408 7 L430 3 L454 6 L484 4 L484 26 L0 26 Z" fill="var(--mustard)"/>
    </svg>
  </section>

</main>
</body>
</html>
```